Elegant and modern Wedding Photography brochure

My existing brochure (attached) needs a major facelift. This is one of the main selling tools - it gets emailed to my clients when they make an equiry on what packages i offer and it is printed out and walked through at our first meeting. This brochure is as critical as my website - it needs to sing!

I'm looking for an eye-catching design that says:
Elegant
Modern
Clean
Crisp
Not cutesy or lovey-dovey thanks - we are more sophisticated and professional than that.

Update images to some of the latest weddings I've shot also. Let me know files and resolution you need. I've enabled right-click to download images on my site for a limited time. Please note that I retain copyright and will pursue any breeches.

Http://www.sarahkelbrin.com/Melbourne-wedding-photography
Updates

Thanks for all of your designs! Will take a few days to decide.

Target Market(s)

Australian Women aged 24-44

Industry/Entity Type

Wedding

Font styles to use
Other font styles liked:
• Century Gothic

Requirements
Must have
• Easy to print - does not have to be 6 A4 pages like the existing brochure
Nice to have
• Some full page images - The photos are supposed to be the hero here :-)
Should not have
• Not cutesy or lovey-dovey thanks - we are more sophisticated and professional than that.

No black backgrounds, I prefer a white thanks

No images in organic shaped boxes (like the rectangles in the logo - no thanks).
Keep the lines straight and sharp

```html
<!DOCTYPE html>
<html lang="en">
<head>
<meta charset="utf-8">
<title>À la Carte Fees to Consider</title>
<link href="https://fonts.googleapis.com/css2?family=Didact+Gothic&display=swap" rel="stylesheet">
<style>
  :root {
    --salmon: #e8917a;
    --salmon-line: #eba08c;
    --teal: #6a9fa8;
    --teal-text: #5f9aa3;
    --paper: #ffffff;
    --rose-light: #f6eeee;
    --rose-mid: #e7d6d6;
  }
  * { box-sizing: border-box; margin: 0; padding: 0; }
  html, body { width: 848px; height: 1200px; overflow: hidden; background: var(--paper); }
  body { font-family: "Didact Gothic", "Century Gothic", sans-serif; }

  .page { position: relative; width: 848px; height: 1200px; background: var(--paper); overflow: hidden; }

  .photo { position: absolute; }
  .photo--bride-sign   { left: 0; top: 0; width: 134px; height: 126px; background: linear-gradient(160deg, #6f7a66, #c9c0b4); }
  .photo--couple-bike  { left: 0; top: 128px; width: 134px; height: 134px; background: linear-gradient(135deg, #5d6f86, #8d5f5a 55%, #4d5660); }
  .photo--pier         { left: 138px; top: 0; width: 402px; height: 262px; background: radial-gradient(ellipse at 50% 45%, #c9cccd, #8e9498 60%, #5c6468); }
  .photo--bouquet      { left: 544px; top: 0; width: 134px; height: 126px; background: radial-gradient(circle at 50% 50%, #f3e6e2, #d9b9b4 70%, #9e8c86); }
  .photo--couple-brick { left: 544px; top: 128px; width: 134px; height: 134px; background: linear-gradient(135deg, #8a5a44, #c69c84 50%, #6e4636); }
  .photo--bride-veil   { left: 680px; top: 0; width: 168px; height: 262px; background: linear-gradient(180deg, #d2d2d2, #9a9a9a 60%, #c4c4c4); }

  .backdrop-roses {
    position: absolute; left: 0; top: 600px; width: 520px; height: 600px;
    background:
      radial-gradient(circle at 18% 90%, var(--rose-mid), transparent 48%),
      radial-gradient(circle at 42% 96%, var(--rose-mid), transparent 36%),
      radial-gradient(circle at 6% 55%, var(--rose-light), transparent 50%);
  }

  .title {
    position: absolute; left: 0; right: 0; top: 268px;
    text-align: center; color: var(--salmon);
    font-size: 62px; line-height: 80px; font-weight: 400;
  }

  .band { position: absolute; top: 376px; height: 624px; width: 26px; background: var(--teal); }
  .band--left { left: 42px; }
  .band--right { left: 788px; }

  .fees {
    position: absolute; left: 68px; top: 376px; width: 720px; height: 624px;
    border-collapse: collapse; table-layout: fixed;
    font-size: 19.5px; line-height: 27px;
    background: rgba(255,255,255,0.55);
  }
  .fees td { border: 1px solid var(--salmon-line); vertical-align: middle; padding: 0; }
  .fees .item { width: 250px; text-align: center; color: var(--teal-text); padding: 0 4px; white-space: nowrap; }
  .fees .price { color: var(--salmon); padding: 0 14px 0 18px; white-space: nowrap; }
</style>
</head>
<body>
<div class="page">
  <div class="photo photo--bride-sign" role="img" aria-label="Bride holding a small 'Bride' sign"></div>
  <div class="photo photo--couple-bike" role="img" aria-label="Couple on a scooter in front of a graffiti wall"></div>
  <div class="photo photo--pier" role="img" aria-label="Couple sitting together looking out over old pier posts"></div>
  <div class="photo photo--bouquet" role="img" aria-label="Bouquet of white and pink roses"></div>
  <div class="photo photo--couple-brick" role="img" aria-label="Smiling couple in front of a brick wall"></div>
  <div class="photo photo--bride-veil" role="img" aria-label="Bride in lace gown and veil holding a bouquet"></div>

  <div class="backdrop-roses" role="img" aria-label="Soft pale roses fading into the page"></div>

  <h1 class="title">À la Carte Fees to Consider</h1>

  <div class="band band--left"></div>
  <div class="band band--right"></div>

  <table class="fees">
    <tr style="height:56px"><td class="item">Engagement Session/<br>Pre-wedding Shoot</td><td class="price">$290 for up to 2 hours of photography on location</td></tr>
    <tr style="height:28px"><td class="item">Digital Negatives</td><td class="price">$490</td></tr>
    <tr style="height:28px"><td class="item">Extended Coverage</td><td class="price">$160 per hour</td></tr>
    <tr style="height:58px"><td class="item">Web Gallery &amp;<br>Socialnest posting</td><td class="price">$160</td></tr>
    <tr style="height:29px"><td class="item">Slideshow</td><td class="price">$250</td></tr>
    <tr style="height:27px"><td class="item">Second Photographer</td><td class="price">$590</td></tr>
    <tr style="height:57px"><td class="item">Client for life</td><td class="price">No sitting fees for portrait sessions –<br>Anniversaries, family portraits, etc: $390</td></tr>
    <tr style="height:56px"><td class="item" rowspan="2">Photo Enlargements</td><td class="price">Quality custom archival prints in a variety of sizes<br>5x7 up to 8x10 $25, 12.5x18.5 $50</td></tr>
    <tr style="height:115px"><td class="price">Stretched Canvas Prints for your wall Various sizes<br>available from 16”x20” starting at $395 through to<br>60’’x96” $1500<br>Plus many other options!</td></tr>
    <tr style="height:57px"><td class="item">Professionally Edited<br>Album (Regular)</td><td class="price">$790</td></tr>
    <tr style="height:56px"><td class="item">Album Upgrade from<br>Regular to Signature Grand</td><td class="price">From Gold Package to Signature Grand: $1150<br>From Platinum Package to Signature Grand: $650</td></tr>
    <tr style="height:57px"><td class="item">Custom Thank-you Cards</td><td class="price">$150 for 50 cards (174mm x 123mm) including<br>envelopes</td></tr>
  </table>
</div>
</body>
</html>
```